Need Business Card for our Real Estate Business with Sales Executive's Picture

PANTONE 484 C ( RED)

PANTONE 2766 C ( BLUE

Industry/Entity Type

Real Estate

Contact Information for Business Card

Name, Mobile, email, & picture of Person
Agency Phone, address, Web address

Requirements
Must have
• Our Logo Colours, Agent Picture,

```html
<!DOCTYPE html>
<html lang="en">
<head>
<meta charset="utf-8">
<title>Meridian Realty – Business Card</title>
<link rel="stylesheet" href="https://fonts.googleapis.com/css2?family=Cinzel:wght@500&family=Jost:ital,wght@0,400;1,400&display=swap">
<style>
  :root {
    --brand-red: #8f1a2a;
    --brand-navy: #1e2a66;
    --paper: #ffffff;
    --paper-shade: #eceef2;
    --ink: #1e2a66;
    --stage: #e4e5e8;
    --photo-light: #c9d0dc;
    --photo-dark: #2b3f86;
  }
  * { box-sizing: border-box; margin: 0; padding: 0; }
  html, body { width: 1200px; height: 864px; overflow: hidden; }
  body {
    background: var(--stage);
    display: flex;
    align-items: center;
    justify-content: center;
    gap: 40px;
    font-family: "Jost", sans-serif;
  }
  .card {
    position: relative;
    width: 520px;
    height: 300px;
    overflow: hidden;
    box-shadow: 0 10px 28px rgba(0,0,0,.18);
  }

  /* Front */
  .card-front {
    background: linear-gradient(180deg, var(--paper-shade) 0%, var(--paper) 40%, var(--paper) 100%);
  }
  .front-brand {
    position: absolute;
    left: 36px;
    top: 48px;
    font-family: "Cinzel", serif;
    font-weight: 500;
    font-size: 30px;
    letter-spacing: 2px;
    color: var(--brand-navy);
  }
  .front-band {
    position: absolute;
    left: 0;
    right: 0;
    top: 100px;
    height: 11px;
    background: var(--brand-navy);
  }
  .agent-photo {
    position: absolute;
    right: 30px;
    top: 34px;
    width: 134px;
    height: 134px;
    border-radius: 50%;
    border: 2px solid var(--brand-navy);
    background: var(--paper);
    padding: 6px;
  }
  .agent-photo-fill {
    width: 100%;
    height: 100%;
    border-radius: 50%;
    background: radial-gradient(circle at 50% 35%, var(--photo-light) 0%, #e9ecf1 45%, var(--photo-dark) 100%);
  }
  .agent-name {
    position: absolute;
    right: 28px;
    top: 176px;
    font-family: "Cinzel", serif;
    font-weight: 500;
    font-size: 21px;
    letter-spacing: 1px;
    color: var(--brand-red);
  }
  .contact-list {
    position: absolute;
    right: 28px;
    top: 208px;
    list-style: none;
    text-align: right;
    font-size: 14px;
    line-height: 20px;
    color: var(--ink);
    letter-spacing: .5px;
  }
  .contact-list li { display: flex; justify-content: flex-end; align-items: center; gap: 9px; }
  .contact-icon { width: 12px; height: 12px; fill: none; stroke: var(--brand-red); stroke-width: 1.6; }
  .office-address {
    position: absolute;
    left: 36px;
    top: 228px;
    font-style: italic;
    font-size: 15px;
    line-height: 19px;
    color: var(--ink);
    letter-spacing: .5px;
  }

  /* Back */
  .card-back { background: var(--brand-navy); }
  .back-panels { position: absolute; inset: 0; }
  .back-brand {
    position: absolute;
    left: 0;
    right: 0;
    top: 210px;
    text-align: center;
    font-family: "Cinzel", serif;
    font-weight: 500;
    font-size: 32px;
    letter-spacing: 3px;
    color: var(--paper);
  }
</style>
</head>
<body>

<section class="card card-front" aria-label="Business card front">
  <div class="front-brand">Meridian Realty</div>
  <div class="front-band"></div>
  <div class="agent-photo">
    <div class="agent-photo-fill" role="img" aria-label="Portrait photo of the sales executive in a navy suit"></div>
  </div>
  <div class="agent-name">Daniel Foster</div>
  <ul class="contact-list">
    <li>(09) 555 0142
      <svg class="contact-icon" viewBox="0 0 12 12"><path d="M2 1.5l2 .2 1 2.5-1.3 1a6 6 0 0 0 3 3l1-1.3 2.6 1 .2 2C7 10.5 1.5 5 2 1.5z"/></svg></li>
    <li>027 555 0198
      <svg class="contact-icon" viewBox="0 0 12 12"><rect x="3" y="1" width="6" height="10" rx="1"/><line x1="5.3" y1="9" x2="6.7" y2="9"/></svg></li>
    <li>daniel@meridianrealty.com
      <svg class="contact-icon" viewBox="0 0 12 12"><rect x="1" y="2.5" width="10" height="7"/><polyline points="1,2.5 6,6.5 11,2.5"/></svg></li>
    <li>www.meridianrealty.com
      <svg class="contact-icon" viewBox="0 0 12 12"><circle cx="6" cy="6" r="5"/><line x1="1" y1="6" x2="11" y2="6"/><ellipse cx="6" cy="6" rx="2.2" ry="5"/></svg></li>
  </ul>
  <address class="office-address">820 Lakeview Avenue Unit 300<br>Fairmont, Il 60410</address>
</section>

<section class="card card-back" aria-label="Business card back">
  <svg class="back-panels" viewBox="0 0 520 300" preserveAspectRatio="none" aria-hidden="true">
    <rect class="back-red" x="0" y="0" width="520" height="300" fill="var(--brand-navy)"/>
    <polygon points="0,0 520,0 520,130 0,40" fill="var(--brand-red)"/>
    <polygon points="0,40 520,130 520,150 0,60" fill="var(--paper)"/>
  </svg>
  <div class="back-brand">Meridian Realty</div>
</section>

</body>
</html>
```